Professional and creative business card design for recruiting service providers

Our company supports German medium-sized companies in filling vacancies promptly. For this we use social media marketing and bring our customers into the visibility.

We want a professional but also creative design for our business cards.

Please look at lindqvar-staff.de to get an impression of our CI.

Target Market(s)

Small and medium-sized companies in Germany from the industry

Industry/Entity Type

Industrie, Handwerk

Contact Information for Business Card

Name, Position, Telefonnummer, Email, Website

Colors
EE7325
F08F49
F5BC92
FAE3D3
FDF4ED

Requirements
Must have
• A picture of the employee and in the style of www.lindqvar-staff.de

```html
<!DOCTYPE html>
<html lang="de">
<head>
<meta charset="utf-8">
<title>Lindqvar &amp; Staff – Visitenkarte</title>
<link href="https://fonts.googleapis.com/css2?family=Montserrat:wght@400;500;700;800&display=swap" rel="stylesheet">
<style>
  :root {
    --orange: #EE7325;
    --orange-soft: #F08F49;
    --ink: #1f1f1f;
    --charcoal: #252525;
    --charcoal-deep: #1a1a1a;
    --paper: #ffffff;
    --stage: #d6d6d6;
  }
  * { box-sizing: border-box; margin: 0; padding: 0; }
  html, body { width: 1200px; height: 788px; overflow: hidden; }
  body {
    background: var(--stage);
    font-family: "Montserrat", sans-serif;
    display: flex;
    align-items: center;
    justify-content: center;
    gap: 40px;
  }
  .card {
    position: relative;
    width: 540px;
    height: 315px;
    border-radius: 22px;
    overflow: hidden;
  }
  .card-front { background: var(--paper); }
  .card-back { background: var(--charcoal); }

  .front-shapes { position: absolute; inset: 0; }

  .portrait {
    position: absolute;
    top: 22px;
    right: 20px;
    width: 200px;
    height: 200px;
    border-radius: 14px 14px 0 0;
    background: linear-gradient(160deg, #3a3a3f 0%, #1d1d22 60%, #2a2a2e 100%);
  }

  .brand {
    position: absolute;
    top: 38px;
    left: 34px;
    display: flex;
    align-items: center;
    gap: 12px;
  }
  .brand-mark {
    width: 40px;
    height: 40px;
    background: var(--orange);
  }
  .brand-name {
    font-weight: 700;
    font-size: 19px;
    line-height: 1.05;
    letter-spacing: 1.5px;
    color: var(--ink);
    text-transform: uppercase;
  }

  .person {
    position: absolute;
    top: 120px;
    left: 34px;
  }
  .person-name {
    font-weight: 800;
    font-size: 20px;
    letter-spacing: 1px;
    color: var(--orange);
    text-transform: uppercase;
  }
  .person-role {
    font-weight: 600;
    font-size: 13px;
    color: var(--ink);
    margin-top: 2px;
  }

  .contact-list {
    position: absolute;
    top: 192px;
    left: 34px;
    list-style: none;
  }
  .contact-item {
    display: flex;
    align-items: center;
    gap: 8px;
    font-size: 13px;
    color: var(--ink);
    line-height: 22px;
  }
  .contact-icon { width: 12px; height: 12px; flex: none; }

  .back-brand {
    position: absolute;
    inset: 0;
    display: flex;
    align-items: center;
    justify-content: center;
    gap: 20px;
  }
  .back-mark {
    width: 70px;
    height: 70px;
    background: var(--charcoal-deep);
  }
  .back-name {
    font-weight: 800;
    font-size: 38px;
    line-height: 1.05;
    letter-spacing: 2px;
    color: var(--charcoal-deep);
    text-transform: uppercase;
  }
</style>
</head>
<body>

  <section class="card card-front">
    <svg class="front-shapes" viewBox="0 0 540 315" width="540" height="315" aria-hidden="true">
      <path d="M150,315 C300,300 450,250 540,185 L540,315 Z" fill="var(--orange)"/>
      <path d="M165,315 C310,305 455,258 540,198 L540,315 Z" fill="var(--paper)"/>
      <path d="M180,315 C320,308 460,262 540,206 L540,315 Z" fill="var(--charcoal)"/>
    </svg>

    <div class="portrait" role="img" aria-label="Porträtfoto des Gründers im dunklen Sakko am Schreibtisch"></div>

    <div class="brand">
      <span class="brand-mark"></span>
      <span class="brand-name">Lindqvar<br>&amp; Staff</span>
    </div>

    <div class="person">
      <p class="person-name">Jonas Lindqvar</p>
      <p class="person-role">Gründer</p>
    </div>

    <ul class="contact-list">
      <li class="contact-item">
        <svg class="contact-icon" viewBox="0 0 24 24"><path fill="var(--orange)" d="M6.6 10.8a15.1 15.1 0 0 0 6.6 6.6l2.2-2.2a1 1 0 0 1 1-.25 11.4 11.4 0 0 0 3.6.57 1 1 0 0 1 1 1V20a1 1 0 0 1-1 1A17 17 0 0 1 3 4a1 1 0 0 1 1-1h3.5a1 1 0 0 1 1 1c0 1.25.2 2.45.57 3.57a1 1 0 0 1-.25 1z"/></svg>
        (030) 555 0142
      </li>
      <li class="contact-item">
        <svg class="contact-icon" viewBox="0 0 24 24"><path fill="var(--orange)" d="M2 5h20v14H2z"/><path fill="none" stroke="#fff" stroke-width="2" d="M2 5l10 8 10-8"/></svg>
        info@lindqvar-staff.de
      </li>
      <li class="contact-item">
        <svg class="contact-icon" viewBox="0 0 24 24"><circle cx="12" cy="12" r="10" fill="var(--orange)"/><path fill="none" stroke="#fff" stroke-width="1.5" d="M2 12h20M12 2c3 3 3 17 0 20M12 2c-3 3-3 17 0 20"/></svg>
        www.lindqvar-staff.de
      </li>
    </ul>
  </section>

  <section class="card card-back">
    <div class="back-brand">
      <span class="back-mark"></span>
      <span class="back-name">Lindqvar<br>&amp; Staff</span>
    </div>
  </section>

</body>
</html>
```